Professional, Attractive, Simple Website Needed!!

We completed the design for our logo.

We need a website built out around this.

Here are a couple samples of how we want ours formatted.

http://brimvoltco.com

http://www.ravelbeam.com/lp/free-quote?LeadSource=Search%20Engine&ProgramName=searchads&experience=qual&language=en&type=brd&gclid=Xk7PLmqwTRZBNVuEYcaHdFgWsLoPeRtQnMxVbCzJaKiOuYtReWqAsDfGhJkLzXcVbNmQwErTyUiOpAsDfGhJkLzX_wcB

http://quorel.co
Updates

Project Deadline Extended
Reason: Extending this deadline due to our delay in providing designers with content for each page. This is coming in next 24 hours.

Project Deadline Extended
Reason: Due to scheduling conflicts and extended travel delays related to Puerto Rico, the deadline has been extended. Your patience is greatly appreciated.

Project Deadline Extended
Reason: Travel and scheduling conflicts have made it impossible to give this project the thorough review it deserves, therefore I am extending the deadline. Thank you for your patience!

Target Market(s)

Home Owners who earn 60k + household annually

Industry/Entity Type

It Professional

Coding

Coded - Design and coding required

Number of Pages Required

5+ page

Font styles to use
Serif

Colors
34a7d8
9bcb3c

Requirements
Must have
• Simple
• Lead form Entry (Ability for visitor to enter Name, number and address for a quote)
• Sleek Design
• Professional
• Testimonials
• Use color Scheme of Design Logo Attached
Nice to have
• Video when site starts
• Like this
• https://www.vidplexa.com/watch?v=Qm8rTbLw3Np&feature=vidplexa.be
Should not have
• Should not include Commercial solar
• Should not include wind power

```html
<!DOCTYPE html>
<html lang="en">
<head>
<meta charset="utf-8">
<title>Brightfield Energy</title>
<link href="https://fonts.googleapis.com/css2?family=Open+Sans:wght@400;600;700&family=Raleway:wght@400;600;700&display=swap" rel="stylesheet">
<style>
:root{
  --blue:#34a7d8;
  --blue-dark:#2b93c2;
  --green:#8dc23c;
  --green-dark:#7ab02f;
  --ink:#333a40;
  --muted:#7b8288;
  --line:#e3e6e9;
  --white:#ffffff;
}
*{box-sizing:border-box;margin:0;padding:0}
html,body{width:1200px;height:2688px;overflow:hidden}
body{font-family:"Open Sans",Arial,sans-serif;color:var(--ink);background:var(--white);position:relative}
.site-header{position:absolute;top:0;left:0;width:1200px;height:92px;background:var(--white);display:flex;align-items:center;justify-content:space-between;padding:0 70px 0 100px}
.brand{display:flex;align-items:center;gap:12px}
.brand-dot{width:44px;height:44px;border-radius:50%;background:var(--blue)}
.brand-name{font-family:"Raleway",sans-serif;font-weight:700;font-size:17px;color:var(--blue);letter-spacing:.5px}
.main-nav{display:flex;gap:34px}
.main-nav a{font-size:12px;font-weight:600;color:var(--ink);text-decoration:none;letter-spacing:.5px;padding:8px 2px}
.main-nav a.active{color:var(--blue);border-bottom:2px solid var(--blue)}
.hero{position:absolute;top:92px;left:0;width:1200px;height:500px;background:linear-gradient(180deg,#a9cbe0 0%,#d6e5ee 45%,#b7c9a2 70%,#6f8f55 100%)}
.hero-title{position:absolute;top:355px;left:290px;font-family:"Raleway",sans-serif;font-weight:700;font-size:40px;color:var(--white);letter-spacing:1px;text-shadow:0 2px 6px rgba(0,0,0,.25)}
.hero-wave{position:absolute;top:520px;left:0;width:1200px;height:100px}
.quote-form{position:absolute;top:162px;left:780px;width:310px;height:400px;background:var(--blue);box-shadow:0 4px 14px rgba(0,0,0,.2)}
.quote-form h2{background:var(--white);font-size:17px;font-weight:700;text-align:center;padding:14px 0;color:var(--ink);letter-spacing:.5px}
.quote-form p{font-size:10px;color:var(--white);text-align:center;padding:16px 30px 10px;line-height:1.5}
.quote-form .field{display:block;margin:12px 28px 0;height:34px;background:var(--white);border:none;font-size:11px;color:var(--muted);padding:0 12px;line-height:34px}
.quote-form .submit{display:block;margin:26px 28px 0;height:40px;background:var(--green);color:var(--white);font-weight:700;font-size:13px;text-align:center;line-height:40px;letter-spacing:.5px}
.welcome{position:absolute;top:610px;left:0;width:1200px;text-align:center}
.section-title{font-family:"Raleway",sans-serif;font-weight:700;font-size:34px;color:var(--green)}
.welcome .lead{width:900px;margin:18px auto 0;font-size:11px;line-height:1.7;color:var(--muted)}
.services{position:absolute;top:740px;left:100px;width:1000px;display:flex;justify-content:space-between}
.service{width:270px;text-align:center;border:1px solid var(--line);padding:0 20px 20px;height:270px;margin-top:80px;position:relative}
.service .photo{width:150px;height:150px;border-radius:50%;margin:-80px auto 0;border:4px solid var(--white);box-shadow:0 2px 6px rgba(0,0,0,.15)}
.service h3{font-size:17px;font-weight:600;margin-top:16px}
.service p{font-size:10px;color:var(--muted);line-height:1.6;margin-top:8px}
.service .more{display:inline-block;margin-top:10px;font-size:10px;font-weight:700;color:var(--green)}
.about{position:absolute;top:1160px;left:0;width:1200px;height:510px;background:linear-gradient(180deg,#6b7580 0%,#55606b 45%,#3d4a5a 100%)}
.about-inner{position:absolute;top:0;left:0;width:100%;text-align:center;padding-top:70px;color:var(--white)}
.about-inner h2{font-family:"Raleway",sans-serif;font-weight:400;font-size:48px}
.about-inner p{width:920px;margin:18px auto 0;font-size:12px;line-height:1.7;opacity:.9}
.btn-outline{display:inline-block;margin-top:150px;border:2px solid var(--white);padding:10px 22px;font-size:13px;font-weight:600;letter-spacing:1px;color:var(--white)}
.testimonials{position:absolute;top:1730px;left:0;width:1200px;text-align:center}
.testimonials h2{font-family:"Raleway",sans-serif;font-weight:700;font-size:34px;color:var(--ink)}
.quote{width:860px;margin:60px auto 0;font-size:12px;line-height:1.8;color:var(--muted);position:relative}
.quote-mark{position:absolute;font-size:60px;color:var(--line);font-family:Georgia,serif;line-height:1}
.quote-mark.open{left:-50px;top:-20px}
.quote-mark.close{right:-50px;bottom:-40px}
.arrow{position:absolute;top:1880px}
.avatar{width:130px;height:130px;border-radius:50%;margin:55px auto 0;background:linear-gradient(180deg,#e2a64a,#8a5a2a)}
.client{margin-top:16px;font-size:12px;font-weight:700;color:var(--green);letter-spacing:1px}
.site-footer{position:absolute;top:2335px;left:0;width:1200px;height:353px;background:var(--blue);text-align:center;color:var(--white)}
.footer-nav{display:flex;justify-content:center;gap:54px;padding-top:34px}
.footer-nav a{font-size:10px;color:var(--white);text-decoration:none;letter-spacing:.5px}
.footer-rule{width:560px;height:1px;background:rgba(255,255,255,.35);margin:20px auto 0}
.contact h2{font-size:20px;font-weight:600;margin-top:28px;letter-spacing:1px}
.contact p{font-size:11px;margin-top:8px}
.contact .icon{display:inline-block;vertical-align:middle;margin-right:6px}
.social{display:flex;justify-content:center;gap:10px;margin-top:26px}
.social span{width:24px;height:24px;border-radius:50%;background:var(--white)}
.copyright{font-size:9px;margin-top:26px;opacity:.85}
</style>
</head>
<body>
<header class="site-header">
  <div class="brand"><span class="brand-dot"></span><span class="brand-name">BRIGHTFIELD ENERGY</span></div>
  <nav class="main-nav">
    <a class="active" href="#">HOME</a><a href="#">ABOUT US</a><a href="#">OUR SERVICES</a><a href="#">BOOK AN APPOINTMENT</a><a href="#">CONTACT US</a>
  </nav>
</header>

<section class="hero" role="img" aria-label="Hero photo: turbines on green hills under a pale morning sky"></section>
<h1 class="hero-title">BRIGHTFIELD ENERGY</h1>
<svg class="hero-wave" viewBox="0 0 1200 100" preserveAspectRatio="none" aria-hidden="true">
  <path d="M0 60 C300 100 500 10 760 40 C950 62 1080 70 1200 30 L1200 100 L0 100 Z" fill="#ffffff"/>
</svg>

<form class="quote-form">
  <h2>REQUEST A FREE QUOTE</h2>
  <p>Send us your details and one of our energy advisers will be in touch within one day.</p>
  <span class="field">Your name</span>
  <span class="field">Your number</span>
  <span class="field">Your address</span>
  <span class="submit">REQUEST A QUOTE NOW</span>
</form>

<section class="welcome">
  <h2 class="section-title">Welcome to Brightfield Energy</h2>
  <p class="lead">We help homeowners cut their monthly bills with clean, reliable home energy systems. From the first survey to the final switch-on, our local team designs, installs and supports every system with care, so you can enjoy lower costs and peace of mind for years ahead.</p>
</section>

<section class="services">
  <article class="service">
    <div class="photo" role="img" aria-label="Photo: hand holding a green leaf" style="background:linear-gradient(135deg,#9ccf4a,#4f8a2a)"></div>
    <h3>Low Cost Energy</h3>
    <p>Smart systems sized for your home, keeping upfront costs fair and monthly bills low from the first day.</p>
    <span class="more">READ MORE &#9656;</span>
  </article>
  <article class="service">
    <div class="photo" role="img" aria-label="Photo: solar panels under a blue sky" style="background:linear-gradient(180deg,#5fb3e3,#2d5f9a)"></div>
    <h3>Higher Energy Service</h3>
    <p>Friendly advisers and certified installers who stay with you through every step of the project.</p>
    <span class="more">READ MORE &#9656;</span>
  </article>
  <article class="service">
    <div class="photo" role="img" aria-label="Photo: technician checking a panel installation" style="background:linear-gradient(180deg,#8fc3e6,#d9653b)"></div>
    <h3>Low Maintenance</h3>
    <p>Durable equipment with simple yearly checks, backed by a clear warranty and responsive support.</p>
    <span class="more">READ MORE &#9656;</span>
  </article>
</section>

<section class="about" role="img" aria-label="Background photo: rows of solar panels with turbines at dusk"></section>
<div class="about-inner" style="top:1160px;position:absolute">
  <h2>About Brightfield Energy</h2>
  <p>We are a family-run team that believes clean power should be simple. Every home we work with gets an honest assessment, a tailored plan and a clear price before any work begins.</p>
  <p>Our installers are trained, insured and local. We take care of permits, paperwork and grid connection, then keep an eye on your system so it performs as promised for many years.</p>
  <span class="btn-outline">READ MORE INFORMATION</span>
</div>

<section class="testimonials">
  <h2>Client Testimonials</h2>
  <div class="quote">
    <span class="quote-mark open">&ldquo;</span>
    From the first call to the final inspection the team was clear, patient and on time. Our bills dropped in the very first month, and every question we had was answered without any pressure. The crew left the house spotless and checked in afterwards to make sure everything was running well. We would happily recommend them to friends and neighbours looking for a simple switch.
    <span class="quote-mark close">&rdquo;</span>
  </div>
  <div class="avatar" role="img" aria-label="Client portrait photo"></div>
  <p class="client">&mdash; MARISA KELLAN</p>
</section>
<svg class="arrow" style="left:40px" width="20" height="30" viewBox="0 0 20 30" aria-hidden="true"><path d="M16 3 L4 15 L16 27" fill="none" stroke="#c9cdd1" stroke-width="2"/></svg>
<svg class="arrow" style="left:1140px" width="20" height="30" viewBox="0 0 20 30" aria-hidden="true"><path d="M4 3 L16 15 L4 27" fill="none" stroke="#c9cdd1" stroke-width="2"/></svg>

<footer class="site-footer">
  <nav class="footer-nav">
    <a href="#">HOME</a><a href="#">ABOUT US</a><a href="#">OUR SERVICES</a><a href="#">BOOK AN APPOINTMENT</a><a href="#">CONTACT US</a>
  </nav>
  <div class="footer-rule"></div>
  <div class="contact">
    <h2>CONTACT INFO</h2>
    <p>Brightfield Energy</p>
    <p><svg class="icon" width="11" height="11" viewBox="0 0 12 12" aria-hidden="true"><path d="M2 1 L4.5 1 L5.5 4 L4 5 C4.7 6.6 5.6 7.5 7 8 L8 6.5 L11 7.5 L11 10 C6 11 1 6 2 1 Z" fill="#fff"/></svg>(555) 014-2278</p>
    <p>hello@brightfieldenergy.com</p>
  </div>
  <div class="social"><span></span><span></span><span></span><span></span><span></span><span></span></div>
  <p class="copyright">&copy; 2024 Brightfield Energy. All rights reserved. Terms of use.</p>
</footer>
</body>
</html>
```